Business Card Design

- one on one personal training
- group personal training
- indoor or outdoor training available
- fitness and health assessments
- personalised fitness programs
- flexible hours for training

I am a Personal Trainer in Perth Australia. I am looking to expand my word of mouth client base.

I would like to see something that uses the colours blue, green and/or yellow.

The final design should reflect the way that I train clients, fun, motivating and perhaps a little quirky?
Updates

update with a logo with the letters MVF thank you

Hi all, Have had some great designs so far. Have decided to go double sided, perhaps to use the back to list my services. Thank you

Please check update brief. Thank you.

Target Market(s)

Professionals, ages 30 to 60

Industry/Entity Type

Training

Contact Information for Business Card

Marla Prentiss
Personal Trainer

0412 807 254
marlafitcoach@quellmail.example
http://www.marlafitcoach.example

Requirements
Must have
• A logo with the letter MVF
Nice to have
• a logo to represent either; fitness, health, change, overall well-being.
Should not have
• Please no weights or lotus flowers!!

```html
<!DOCTYPE html>
<html lang="en">
<head>
<meta charset="utf-8">
<title>Marla Prentiss – Personal Trainer Business Card</title>
<link rel="stylesheet" href="https://fonts.googleapis.com/css2?family=Source+Sans+3:wght@400;600&display=swap">
<style>
  :root {
    --backdrop: #3c3c3c;
    --card: #ffffff;
    --ink: #1e1e1e;
    --brand-blue: #1a72bb;
    --sun-yellow: #ffcc00;
    --field-green: #4aae3a;
    --sky-blue: #1b7cc4;
    --dot-teal: #129a8c;
    --dot-orange: #f39a1e;
    --dot-yellow: #f5c800;
    --dot-lime: #8dc63f;
    --dot-blue: #1a6fb8;
  }
  * { margin: 0; padding: 0; box-sizing: border-box; }
  html, body {
    width: 1200px;
    height: 824px;
    overflow: hidden;
    background: var(--backdrop);
    font-family: "Source Sans 3", sans-serif;
    color: var(--ink);
  }
  .card {
    position: absolute;
    left: 50px;
    top: 71px;
    width: 1100px;
    height: 682px;
    background: var(--card);
  }
  .identity {
    position: absolute;
    left: 60px;
    width: 470px;
    text-align: center;
  }
  .identity__name {
    top: 250px;
    font-size: 50px;
    font-weight: 600;
    color: var(--brand-blue);
    letter-spacing: -0.5px;
    line-height: 1;
  }
  .identity__role {
    top: 313px;
    font-size: 29px;
    font-weight: 400;
    line-height: 1;
  }
  .contact {
    position: absolute;
    left: 60px;
    width: 490px;
    text-align: center;
    font-size: 26px;
    line-height: 1;
  }
  .contact__phone { top: 398px; }
  .contact__online { top: 519px; line-height: 34px; }
  .hero-art {
    position: absolute;
    left: 585px;
    top: 49px;
    width: 472px;
    height: 330px;
    overflow: hidden;
    background:
      radial-gradient(circle at 105% 115%, var(--field-green) 0 55%, transparent 55.5%),
      radial-gradient(circle at 0% 110%, var(--sky-blue) 0 22%, transparent 22.5%),
      linear-gradient(135deg, var(--sun-yellow) 0%, #ffc21a 55%, var(--sky-blue) 100%);
  }
  .brand-badge {
    position: absolute;
    right: 0;
    bottom: 0;
    width: 190px;
    height: 150px;
  }
  .brand-badge__name {
    position: absolute;
    left: 50px;
    top: 54px;
    font-size: 48px;
    font-weight: 600;
    color: var(--brand-blue);
    line-height: 1;
  }
  .services {
    position: absolute;
    left: 589px;
    top: 398px;
    list-style: none;
    font-size: 26px;
    line-height: 1;
  }
  .services li {
    display: flex;
    align-items: center;
    height: 39.5px;
  }
  .services li::before {
    content: "";
    width: 15px;
    height: 15px;
    border-radius: 50%;
    margin-right: 19px;
    background: var(--bullet);
  }
  .services .teal { --bullet: var(--dot-teal); }
  .services .orange { --bullet: var(--dot-orange); }
  .services .yellow { --bullet: var(--dot-yellow); }
  .services .lime { --bullet: var(--dot-lime); }
  .services .blue { --bullet: var(--dot-blue); }
</style>
</head>
<body>
  <main class="card">
    <h1 class="identity identity__name">Marla Prentiss</h1>
    <p class="identity identity__role">Personal Trainer</p>

    <p class="contact contact__phone">Phone : 0412 807 254</p>
    <p class="contact contact__online">
      E-mail: marlafitcoach@quellmail.example<br>
      Website: www.marlafitcoach.example
    </p>

    <div class="hero-art" role="img" aria-label="Illustration of a silhouetted figure stretching in a yoga pose over yellow, green and blue arcs">
      <div class="brand-badge">
        <svg width="190" height="150" viewBox="0 0 190 150" aria-hidden="true">
          <circle cx="110" cy="95" r="78" fill="#ffffff"/>
        </svg>
        <span class="brand-badge__name">MVF</span>
      </div>
    </div>

    <ul class="services">
      <li class="teal">One on one personal training</li>
      <li class="orange">Group personal training</li>
      <li class="yellow">Indoor or outdoor training available</li>
      <li class="lime">Fitness and health assessments</li>
      <li class="blue">Personalised fitness programs</li>
    </ul>
  </main>
</body>
</html>
```